Venora Tulesi Parwine

Design a self adhesive label to be placed on a standard 1 pint milk plastic bottle 14.acm x 5.5 cm and 1 litre plastic bottle 17cm X 6.1cm

The product to be packed inside the bottle is a Natural Fermented Milk which looks between Natural Yogurt but with curdle inside.

I have update project to a guaranteed contest

Target Market(s)

Small Ethnic African Community from Southern Africa

Industry/Entity Type

Plastic

Requirements
Must have
• Logo/Brand VENORA and Product Name which is a double word TULESI PARWINE.

```html
<!DOCTYPE html>
<html lang="en">
<head>
<meta charset="utf-8">
<title>Venora Tulesi Parwine – bottle label</title>
<link rel="stylesheet" href="https://fonts.googleapis.com/css2?family=Chewy&family=Londrina+Solid:wght@400&family=Cousine&family=Open+Sans:wght@400;600&display=swap">
<style>
  :root{
    --page:#f2f2f0;
    --label-white:#fbfbfa;
    --plum:#7a3c6a;
    --leaf:#6e9c3c;
    --leaf-dark:#4f7a28;
    --dot-field:#bcd69a;
    --cream:#f4efb2;
    --panel:#e8e4ef;
    --ink:#4a4a52;
  }
  *{margin:0;padding:0;box-sizing:border-box}
  html,body{width:1200px;height:900px;overflow:hidden;background:var(--page)}
  .canvas{position:relative;width:1200px;height:900px}
  .label{
    position:absolute;left:100px;top:230px;width:1000px;height:440px;
    background:var(--label-white);overflow:hidden;
    box-shadow:0 2px 10px rgba(0,0,0,.12);
  }
  .volume{
    position:absolute;left:34px;top:26px;
    font-family:"Cousine",monospace;font-size:26px;color:var(--ink);letter-spacing:1px;
  }
  .product-first{
    position:absolute;left:30px;top:92px;
    font-family:"Londrina Solid",sans-serif;font-size:118px;line-height:1;
    color:var(--plum);letter-spacing:2px;
  }
  .brand-band{
    position:absolute;left:560px;top:74px;width:80px;height:170px;
    background:var(--leaf);display:flex;align-items:center;justify-content:center;
  }
  .brand-name{
    transform:rotate(-90deg);white-space:nowrap;
    font-family:"Open Sans",sans-serif;font-weight:600;font-size:34px;color:var(--label-white);
    letter-spacing:1px;
  }
  .dot-field{
    position:absolute;left:0;top:244px;width:640px;height:196px;background:var(--dot-field);
  }
  .product-second{
    position:absolute;left:26px;top:256px;
    font-family:"Chewy",cursive;font-size:112px;line-height:1;
    color:var(--cream);-webkit-text-stroke:4px var(--leaf-dark);paint-order:stroke fill;
    letter-spacing:3px;
  }
  .nutrition{
    position:absolute;left:640px;top:0;width:360px;height:440px;background:var(--panel);
    font-family:"Open Sans",sans-serif;color:var(--ink);
  }
  .nutrition-title{
    margin-top:60px;background:var(--leaf);color:var(--label-white);
    font-size:24px;font-weight:400;padding:8px 18px;
  }
  .nutrition-note{font-size:15px;line-height:1.35;padding:14px 18px 10px}
  .nutrition-table{width:calc(100% - 36px);margin:0 18px;border-collapse:collapse;font-size:16px}
  .nutrition-table td{padding:5px 0;border-bottom:1px solid #cfc8da}
  .nutrition-table td.value{text-align:right}
</style>
</head>
<body>
<div class="canvas">
  <section class="label">
    <p class="volume">568ml 1pint e</p>
    <h1 class="product-first">TULESI</h1>
    <div class="brand-band"><span class="brand-name">venora</span></div>
    <div class="dot-field" role="img" aria-label="Light green polka-dot pattern background"></div>
    <h2 class="product-second">PARWINE</h2>
    <aside class="nutrition">
      <h3 class="nutrition-title">Nutritional Information</h3>
      <p class="nutrition-note">Percentages of guideline daily amounts for adults. Typical values per 100ml serving.</p>
      <table class="nutrition-table">
        <tr><td>Energy</td><td class="value">292 kJ</td></tr>
        <tr><td>Protein</td><td class="value">3.3 g</td></tr>
        <tr><td>Fat</td><td class="value">3.5 g</td></tr>
        <tr><td>Carbohydrate</td><td class="value">4.5 g</td></tr>
        <tr><td>Calcium</td><td class="value">120 mg</td></tr>
      </table>
    </aside>
  </section>
</div>
</body>
</html>
```